Development of the overall look and feel for the website. www.ReelPalsHub.com

This site is geared as a competitor to some of the major Fan websites. Where we want to be different is making a site geared more towards interaction with the Fans in the Social Media platform.
-Live streaming
-Instant Messaging
-Ability to request and purchase custom digital pieces
-Ability for Models/creators to sell blogs, podcasts, clips, screensavers, etc. through a dedicated online digital store.
-We will also have story like features similar to those found on Photoburst to allow interaction.
-Content Creators keep 85% of earnings

This should be sexy, seductive, bold, and geared towards all spectrums. From Swingers, Kink, Fetish, Milf, College, etc.

Overall the feeling should be Fun with a sense of excitement that is taboo and erotic while not scaring people away.

Trying to find the perfect blend between finding harmony/Norma Whitcombe/GBT/SoloPatron/Velvet Soiree and KRV. Monetization will be most similar to SoloPatron.

Target Market(s)

Target market should be 18+ / All Genders/ All sexuality. I want to be sure to target markets that were traditionally left out from some of the bigger platforms with all lifestyle and gender inclusion.

Industry/Entity Type

Adult Modeling, Adult Website, Streaming, Porn/fetish

Colors

Designer to choose colors to be used in the design.

Requirements
Must have
• Sex Appeal, Curiosity, Call to action, Storyboard to tell what we are about
Nice to have
• uploaded some designs that have overall look/feel.
Should not have
• Sexy but no nudity

```html
<!DOCTYPE html>
<html lang="en">
<head>
<meta charset="utf-8">
<title>ReelPalsHub – Live Meet</title>
<link href="https://fonts.googleapis.com/css2?family=Poppins:wght@400;500;600&display=swap" rel="stylesheet">
<style>
:root{
  --brand:#a82862;
  --brand-soft:#d9a2be;
  --ink:#1b1b1b;
  --title:#9b2336;
  --panel:#e0dcdd;
  --chip:#e4e1e2;
  --white:#ffffff;
  --rec:#ee4436;
  --teal:#2e9a7f;
  --photo-a:#2a2a2e;
  --photo-b:#5b5a63;
}
*{box-sizing:border-box;margin:0;padding:0}
html,body{width:1200px;height:857px;overflow:hidden;background:var(--white)}
body{position:relative;font-family:'Poppins',sans-serif;color:var(--ink)}
.abs{position:absolute}
.sidebar{left:0;top:0;width:75px;height:857px;border-right:3px solid #ededed}
.nav-icon{left:18px;width:26px;height:26px}
.nav-active{left:73px;top:123px;width:5px;height:33px;background:var(--brand)}
.avatar{border-radius:50%;background:radial-gradient(circle at 40% 40%,var(--photo-b),var(--photo-a))}
.search{left:110px;top:36px;width:223px;height:43px;background:var(--brand);border-radius:15px;color:var(--white);font-size:16px;display:flex;align-items:center}
.search span{flex:1;padding-left:21px}
.search .go{width:56px;height:100%;border-left:2px solid var(--white);display:flex;align-items:center;justify-content:center}
.brand-name{left:430px;top:55px;width:142px;text-align:center;font-size:15px;font-weight:600;color:var(--title);display:flex;align-items:center;justify-content:center;gap:6px}
.brand-name i{width:10px;height:10px;border-radius:50%;background:var(--title);display:inline-block}
.meet-title{left:340px;top:122px;width:302px;text-align:center;font-size:21px;color:var(--title)}
.record{left:146px;top:138px;display:flex;align-items:center;gap:11px;font-size:16px}
.rec-dot{width:22px;height:22px;border-radius:50%;background:var(--rec);display:flex;align-items:center;justify-content:center}
.rec-dot::after{content:"";width:9px;height:9px;border-radius:50%;background:var(--white)}
.invite{left:707px;top:41px;display:flex;align-items:center;gap:6px;font-size:15px}
.invite b{width:27px;height:27px;border-radius:50%;background:var(--brand);color:var(--white);display:flex;align-items:center;justify-content:center;font-weight:400;font-size:20px}
.close{left:706px;top:132px;width:129px;height:34px;border-radius:17px;background:var(--brand);color:var(--white);font-size:17px;display:flex;align-items:center;justify-content:space-between;padding:0 20px}
.stage{left:107px;top:176px;width:711px;height:507px;border-radius:60px;overflow:hidden;background:linear-gradient(120deg,#1b1b20 0%,#4b4a52 45%,#8d8d96 70%,#2a2a30 100%)}
.live{left:144px;top:202px;width:69px;height:39px;border-radius:10px;background:var(--brand);color:var(--white);font-size:16px;display:flex;align-items:center;justify-content:center}
.thumb{left:746px;width:85px;height:87px;border-radius:14px;background:linear-gradient(140deg,#151515,#4e4a4c);border:1px solid #ccc}
.thumb-badge{left:817px;width:25px;height:25px;border-radius:50%;display:flex;align-items:center;justify-content:center}
.badge-rec{background:var(--rec)}
.badge-rec::after{content:"";width:9px;height:9px;border-radius:50%;background:var(--white)}
.badge-cam{background:var(--teal)}
.caption{left:195px;top:596px;width:566px;height:60px;border-radius:16px;background:rgba(70,40,60,.55);color:var(--white);font-size:14px;font-weight:500;display:flex;align-items:center;padding-left:26px}
.volume{left:101px;top:735px;width:160px;height:57px;border-radius:16px;background:var(--chip);display:flex;align-items:center;padding-left:6px;gap:10px}
.ctl{top:732px;width:52px;height:65px;border-radius:16px;background:var(--chip);display:flex;align-items:center;justify-content:center}
.ctl-on{background:var(--brand-soft)}
.label{top:802px;font-size:16px;text-align:center}
.panel{left:857px;top:33px;width:343px;height:783px;background:var(--panel);border-radius:18px 0 0 18px}
.tabs{left:878px;top:51px;width:300px;height:64px;border-radius:14px;background:var(--white)}
.tab-on{left:883px;top:58px;width:149px;height:47px;border-radius:14px;background:var(--brand);color:var(--white);font-size:15px;display:flex;align-items:center;justify-content:center}
.tab-off{left:1032px;top:58px;width:140px;height:47px;font-size:15px;display:flex;align-items:center;justify-content:center}
.stream{left:878px;top:132px;width:296px;height:199px;border-radius:16px;background:var(--brand);color:var(--white)}
.stream h3{font-weight:500;font-size:16px;text-align:center;height:63px;line-height:63px;border-bottom:1px solid rgba(255,255,255,.3)}
.bar{position:absolute;left:15px;width:265px;height:5px;border-radius:3px;background:rgba(255,255,255,.35)}
.bar i{display:block;height:100%;border-radius:3px;background:var(--white)}
.stat{position:absolute;left:15px;width:265px;display:flex;justify-content:space-between;font-size:16px;font-weight:500;line-height:22px}
.stat-hi{position:absolute;left:13px;top:119px;width:270px;height:46px;border-radius:14px;background:rgba(255,255,255,.12)}
.divider{left:876px;top:349px;width:298px;display:flex;align-items:center;gap:12px;font-size:16px}
.divider::before,.divider::after{content:"";flex:1;height:1px;background:var(--brand)}
.who{font-size:16px}
.bubble{background:var(--white);border-radius:14px;font-size:14px;display:flex;align-items:center;padding-left:18px}
.compose{left:878px;top:737px;width:301px;height:55px;border-radius:14px;background:var(--white);display:flex;align-items:center;padding-left:13px;gap:17px;font-size:16px}
.send{left:1123px;top:742px;width:51px;height:46px;border-radius:14px;background:var(--brand);display:flex;align-items:center;justify-content:center}
</style>
</head>
<body>

<aside class="abs sidebar">
  <svg class="abs nav-icon" style="top:42px" viewBox="0 0 24 24"><path d="M12 2 1 12h3v10h6v-6h4v6h6V12h3z" fill="#111"/></svg>
  <svg class="abs nav-icon" style="top:124px;width:30px" viewBox="0 0 30 24"><rect x="1" y="5" width="19" height="14" rx="2" fill="var(--brand)"/><path d="M21 10l8-5v14l-8-5z" fill="var(--brand)"/></svg>
  <svg class="abs nav-icon" style="top:206px" viewBox="0 0 24 24"><path d="M6 17V11a6 6 0 0 1 12 0v6l2 2H4zM10 21h4" fill="none" stroke="#111" stroke-width="1.6"/></svg>
  <svg class="abs nav-icon" style="top:289px" viewBox="0 0 24 24"><path d="M12 3C6 3 2 7 2 11.5c0 2.5 1.3 4.6 3.3 6L4 21l4.4-2C9.5 19.5 10.7 20 12 20c6 0 10-4 10-8.5S18 3 12 3z" fill="#111"/><circle cx="8" cy="11.5" r="1.4" fill="#fff"/><circle cx="12" cy="11.5" r="1.4" fill="#fff"/><circle cx="16" cy="11.5" r="1.4" fill="#fff"/></svg>
  <svg class="abs nav-icon" style="top:371px;width:30px" viewBox="0 0 30 24"><g fill="none" stroke="#111" stroke-width="1.5"><circle cx="15" cy="5" r="3"/><circle cx="7" cy="8" r="2.6"/><circle cx="23" cy="8" r="2.6"/><path d="M10 22v-7a5 5 0 0 1 10 0v7zM2 22v-6a4 4 0 0 1 7-2M28 22v-6a4 4 0 0 0-7-2"/></g></svg>
  <svg class="abs nav-icon" style="top:453px;width:30px" viewBox="0 0 30 24"><g fill="none" stroke="#111" stroke-width="1.5"><circle cx="5" cy="12" r="2.5"/><circle cx="15" cy="12" r="2.5"/><circle cx="25" cy="12" r="2.5"/></g></svg>
  <div class="abs avatar" style="left:10px;top:736px;width:54px;height:54px" role="img" aria-label="Profile photo of the signed-in creator"></div>
</aside>
<div class="abs nav-active"></div>

<div class="abs search"><span>Serach Here</span><div class="go"><svg width="26" height="26" viewBox="0 0 24 24"><circle cx="10" cy="10" r="7" fill="none" stroke="#fff" stroke-width="2"/><path d="M15 15l6 6" stroke="#fff" stroke-width="2"/></svg></div></div>

<div class="abs brand-name"><i></i>ReelPalsHub</div>
<div class="abs meet-title">Meet - Velvet Ember</div>

<div class="abs record"><span class="rec-dot"></span><span>Record&nbsp;&nbsp;00.56.23</span></div>
<div class="abs invite"><b>+</b>Invite People</div>
<div class="abs close"><span>Close</span><span style="font-size:15px">✕</span></div>

<div class="abs stage" role="img" aria-label="Live stream video of the creator couple, moody black and white"></div>
<div class="abs live">Live</div>

<div class="abs thumb" style="top:237px" role="img" aria-label="Participant video thumbnail"></div>
<div class="abs thumb" style="top:334px" role="img" aria-label="Participant video thumbnail"></div>
<div class="abs thumb" style="top:431px" role="img" aria-label="Participant video thumbnail"></div>
<div class="abs thumb" style="top:528px" role="img" aria-label="Participant video thumbnail"></div>
<div class="abs thumb-badge badge-rec" style="top:268px"></div>
<div class="abs thumb-badge badge-cam" style="top:368px"><svg width="14" height="10" viewBox="0 0 14 10"><rect width="9" height="10" rx="1" fill="#fff"/><path d="M9 4l5-3v8L9 6z" fill="#fff"/></svg></div>
<div class="abs thumb-badge badge-cam" style="top:460px"><svg width="14" height="10" viewBox="0 0 14 10"><rect width="9" height="10" rx="1" fill="#fff"/><path d="M9 4l5-3v8L9 6z" fill="#fff"/></svg></div>
<div class="abs thumb-badge badge-rec" style="top:556px"></div>

<div class="abs caption">Hello guys REELPALSHUB.COM</div>

<div class="abs volume">
  <svg width="32" height="28" viewBox="0 0 24 24"><path d="M3 9h4l5-4v14l-5-4H3z" fill="#111"/><path d="M15 9a4 4 0 0 1 0 6M17.5 6.5a7.5 7.5 0 0 1 0 11" fill="none" stroke="#111" stroke-width="1.8"/></svg>
  <svg width="100" height="10" viewBox="0 0 100 10"><rect x="0" y="3.5" width="54" height="3" rx="1.5" fill="var(--brand)"/><circle cx="56" cy="5" r="4.5" fill="var(--brand)"/><rect x="65" y="3.5" width="27" height="3" rx="1.5" fill="#fff"/></svg>
</div>
<div class="abs ctl" style="left:326px"><svg width="22" height="28" viewBox="0 0 22 28"><rect x="7" y="2" width="8" height="15" rx="4" fill="none" stroke="#333" stroke-width="1.6"/><path d="M3 13a8 8 0 0 0 16 0M11 21v5" fill="none" stroke="#333" stroke-width="1.6"/></svg></div>
<div class="abs ctl ctl-on" style="left:417px"><svg width="24" height="20" viewBox="0 0 24 20"><rect x="2" y="5" width="14" height="11" rx="2" fill="#fff"/><path d="M16 9l6-3v9l-6-3z" fill="#fff"/><path d="M3 19L20 2" stroke="var(--brand-soft)" stroke-width="2"/></svg></div>
<div class="abs ctl" style="left:508px"><svg width="26" height="26" viewBox="0 0 24 24"><path d="M20 11l-8.5 8.5a5 5 0 0 1-7-7L13 4a3.3 3.3 0 0 1 4.7 4.7L9.2 17.2a1.7 1.7 0 0 1-2.4-2.4L14.5 7" fill="none" stroke="#333" stroke-width="1.6"/></svg></div>
<div class="abs ctl" style="left:599px"><svg width="24" height="20" viewBox="0 0 24 20"><rect x="2" y="2" width="20" height="13" rx="1" fill="none" stroke="#333" stroke-width="1.5"/><circle cx="12" cy="8.5" r="3" fill="none" stroke="#333" stroke-width="1.3"/><path d="M8 18h8" stroke="#333" stroke-width="1.5"/></svg></div>
<div class="abs ctl" style="left:771px"><svg width="24" height="24" viewBox="0 0 24 24"><path d="M14 4H5v16h9M10 12h11M17 8l4 4-4 4" fill="none" stroke="#333" stroke-width="1.6"/></svg></div>

<div class="abs label" style="left:104px">Volume</div>
<div class="abs label" style="left:312px;width:80px">mic</div>
<div class="abs label" style="left:403px;width:80px">video</div>
<div class="abs label" style="left:494px;width:80px">Clips</div>
<div class="abs label" style="left:574px;width:120px">Screen Saver</div>
<div class="abs label" style="left:757px;width:80px">Next</div>

<section class="abs panel"></section>
<div class="abs tabs"></div>
<div class="abs tab-on">Messages(4)</div>
<div class="abs tab-off">Participant(5)</div>

<div class="abs stream">
  <h3>Live Streaming</h3>
  <div class="bar" style="top:86px"><i style="width:65%"></i></div>
  <div class="stat" style="top:91px"><span>Photoburst</span><span>75%</span></div>
  <div class="stat-hi"></div>
  <div class="bar" style="top:140px"><i style="width:50%"></i></div>
  <div class="stat" style="top:168px"><span>Friendnest</span><span>60%</span></div>
</div>

<div class="abs divider">Message</div>

<div class="abs avatar" style="left:871px;top:382px;width:60px;height:60px" role="img" aria-label="Jorge profile photo"></div>
<div class="abs who" style="left:944px;top:389px">Jorge</div>
<div class="abs bubble" style="left:941px;top:418px;width:175px;height:40px">HI</div>

<div class="abs avatar" style="left:871px;top:461px;width:60px;height:60px" role="img" aria-label="Riley profile photo"></div>
<div class="abs who" style="left:943px;top:465px">Riley</div>
<div class="abs bubble" style="left:939px;top:499px;width:132px;height:39px">Hello</div>

<div class="abs who" style="left:1129px;top:538px">You</div>
<div class="abs bubble" style="left:1001px;top:571px;width:177px;height:39px;justify-content:flex-end;padding:0 23px 0 0">Hi</div>

<div class="abs avatar" style="left:871px;top:615px;width:60px;height:60px" role="img" aria-label="Patricia profile photo"></div>
<div class="abs who" style="left:943px;top:617px">Patricia</div>
<div class="abs bubble" style="left:941px;top:648px;width:219px;height:60px">Good Morning</div>

<div class="abs compose">
  <svg width="20" height="20" viewBox="0 0 20 20"><rect x="1.5" y="2.5" width="17" height="15" rx="1.5" fill="none" stroke="#333" stroke-width="1.3"/><circle cx="7" cy="7.5" r="1.6" fill="none" stroke="#333" stroke-width="1.2"/><path d="M2 16l5-5 3 3 3-4 5 6" fill="none" stroke="#333" stroke-width="1.2"/></svg>
  <span>Write a message</span>
</div>
<div class="abs send"><svg width="22" height="22" viewBox="0 0 24 24"><path d="M22 2L2 10l8 3 3 8zM10 13l12-11" fill="none" stroke="#fff" stroke-width="1.6" stroke-linejoin="round"/></svg></div>

</body>
</html>
```